Steadfast hearts flyer

Benefits of prayer
- Prayer connects you to the God of fullness. Gal. 6:8
- Prayer places you cares on the Lord. 1 Peter 5:7, Matt. 11:28
- Prayer makes you fruitful in the vineyard of the Lord-this brings honour and glory. John 15:2
- Through prayer you exercise your Kingly authority. Matt. 16:19, 18:19.
- Prayer transforms you to be like Him. Luke 9:29.
- Prayer quickens divine inheritance. Luke 5:3-6
- Prayer will stir divine potentials in you. 2 Tim. 1:6
- And many more!

Experience the might and possibilities of prayer.

Join the Steadfast Hearts Ministry!

```html
<!DOCTYPE html>
<html lang="en">
<head>
<meta charset="utf-8">
<title>Steadfast Hearts flyer</title>
<link href="https://fonts.googleapis.com/css2?family=Fira+Sans+Condensed:ital,wght@1,400;1,700&family=Great+Vibes&display=swap" rel="stylesheet">
<style>
  :root {
    --backdrop: #2b2b2b;
    --ink: #1e3a78;
    --ink-soft: #2a4d8f;
    --logo-green: #7aa63a;
    --sky-top: #ffffff;
    --sky-mid: #cfe4f3;
    --sky-deep: #3d97d3;
    --horizon: #eef4f6;
    --field: #a58b5a;
    --field-dark: #5e4a2c;
    --white: #ffffff;
  }
  html, body {
    margin: 0;
    width: 1200px;
    height: 1092px;
    overflow: hidden;
    background: var(--backdrop);
  }
  .flyer {
    position: absolute;
    left: 205px;
    top: 46px;
    width: 790px;
    height: 1000px;
    overflow: hidden;
    font-family: "Fira Sans Condensed", "Arial Narrow", sans-serif;
    font-style: italic;
    color: var(--ink);
  }
  .flyer__scene {
    position: absolute;
    inset: 0;
    background:
      radial-gradient(ellipse 140px 260px at 50% 52%, rgba(255,255,255,0.85), rgba(255,255,255,0) 70%),
      linear-gradient(180deg,
        var(--sky-top) 0%,
        var(--sky-top) 16%,
        var(--sky-mid) 32%,
        var(--sky-deep) 50%,
        #8cc3e6 66%,
        var(--horizon) 74%,
        var(--field) 77%,
        #8a7246 88%,
        var(--field-dark) 100%);
  }
  .brand {
    position: absolute;
    left: 138px;
    top: 32px;
    display: flex;
    align-items: center;
    gap: 18px;
  }
  .brand__mark {
    width: 102px;
    height: 102px;
    border-radius: 50%;
    background: var(--logo-green);
  }
  .brand__name {
    font-size: 34px;
    font-weight: 400;
    color: var(--ink);
    line-height: 1.1;
    max-width: 340px;
  }
  .title {
    position: absolute;
    top: 188px;
    left: 0;
    right: 0;
    margin: 0;
    text-align: center;
    font-family: "Great Vibes", cursive;
    font-style: normal;
    font-weight: 400;
    font-size: 62px;
    color: var(--ink);
  }
  .benefit {
    position: absolute;
    margin: 0;
    font-size: 25px;
    line-height: 38px;
  }
  .benefit--center { left: 0; right: 0; text-align: center; }
  .benefit--connects { top: 262px; }
  .benefit--cares { top: 300px; }
  .benefit--fruitful { left: 47px; top: 350px; width: 260px; }
  .benefit--authority { left: 486px; top: 350px; width: 270px; }
  .benefit--inheritance { left: 74px; top: 548px; width: 230px; }
  .benefit--transforms { left: 493px; top: 548px; width: 270px; }
  .benefit--potentials { top: 645px; }
  .more {
    position: absolute;
    left: 430px;
    top: 712px;
    margin: 0;
    font-family: "Great Vibes", cursive;
    font-style: normal;
    font-size: 34px;
    color: var(--ink);
  }
  .call {
    position: absolute;
    left: 0;
    right: 0;
    margin: 0;
    text-align: center;
    font-weight: 700;
    letter-spacing: -0.5px;
  }
  .call--experience {
    top: 884px;
    font-size: 33px;
    color: var(--white);
    text-shadow: 0 0 3px #1b2433, 1px 2px 3px #1b2433;
  }
  .call--join {
    top: 932px;
    font-size: 36px;
    color: var(--ink);
    text-shadow: 0 0 2px var(--white), 0 0 4px var(--white), 0 0 6px var(--white);
  }
</style>
</head>
<body>
  <article class="flyer">
    <div class="flyer__scene" role="img" aria-label="Photograph: bright blue sky with soft clouds and a glowing cross, above a dirt road through golden grass fields with a lone hiker walking away"></div>

    <header class="brand">
      <div class="brand__mark"></div>
      <div class="brand__name">Harvest Brothers Fellowship</div>
    </header>

    <h1 class="title">Benefits of prayer</h1>

    <p class="benefit benefit--center benefit--connects">Prayer connects you to the God of fullness. Gal. 6:8</p>
    <p class="benefit benefit--center benefit--cares">Prayer places you cares on the Lord. 1 Peter 5:7, Matt. 11:28</p>
    <p class="benefit benefit--fruitful">Prayer makes you fruitful in the vineyard of the Lord-this brings honour and glory. John 15:2</p>
    <p class="benefit benefit--authority">Through prayer you exercise your Kingly authority. Matt. 16:19, 18:19.</p>
    <p class="benefit benefit--inheritance">Prayer quickens divine inheritance. Luke 5:3-6</p>
    <p class="benefit benefit--transforms">Prayer transforms you to be like Him. Luke 9:29.</p>
    <p class="benefit benefit--center benefit--potentials">Prayer will stir divine potentials in you. 2 Tim. 1:6</p>

    <p class="more">And many more!</p>

    <p class="call call--experience">Experience the might and possibilities of prayer.</p>
    <p class="call call--join">Join the Steadfast Hearts Ministry!</p>
  </article>
</body>
</html>
```